Website for new dental office

I am Dr. Colin Ashford and am building a new dental practice. I specialize in general dentistry. I am young and have a higher end dental practice incorporating very new technologies and would like my website to reflect that. As many dental patients are older, the website must be very easy to navigate. I would like patients to be able to request appointments, and will eventually add on patient information forms (the health history, etc, that you normally fill out in the practice) from my practice management software, so leave an area for that.

Industry/Entity Type

Building

```html
<!DOCTYPE html>
<html lang="en">
<head>
<meta charset="utf-8">
<title>Colin Ashford, DDS – General Dentistry</title>
<link rel="stylesheet" href="https://fonts.googleapis.com/css2?family=Open+Sans:wght@300;400;600&display=swap">
<style>
:root{
  --brand:#3f5ca8;
  --nav-top:#6a7cb0;
  --nav-bottom:#4e5f95;
  --nav-active:#6f93dc;
  --btn:#4d5c8e;
  --btn-dark:#3c4a78;
  --ink:#1f1f1f;
  --text:#555;
  --muted:#8a8a8a;
  --line:#d8d8d8;
  --band:#f4f4f4;
  --footer:#1c1c1c;
  --footer-bar:#111;
  --footer-text:#d9d9d9;
  --green:#3a8c3f;
  --white:#fff;
}
*{box-sizing:border-box;margin:0;padding:0}
html,body{width:1200px;height:2281px;overflow:hidden}
body{position:relative;background:var(--white);font-family:"Open Sans",Arial,sans-serif;color:var(--text)}
.abs{position:absolute}

/* header */
.logo{left:120px;top:34px;font-size:34px;font-weight:400;letter-spacing:2px;color:var(--brand);text-transform:uppercase}
.callout{right:120px;top:22px;text-align:right}
.callout .phone{font-size:24px;color:#444;font-weight:300;padding-right:44px}
.callout .phone b{font-weight:600;color:#333}
.callout .tag{font-size:17px;color:var(--brand);margin-top:2px}
.callout svg{position:absolute;right:0;top:4px}

/* nav */
.nav{left:0;top:105px;width:1200px;height:44px;background:linear-gradient(var(--nav-top),var(--nav-bottom))}
.nav ul{list-style:none;display:flex;position:absolute;left:120px;top:0;height:44px}
.nav li{height:44px;line-height:44px;padding:0 22px;color:var(--white);font-size:14px}
.nav li.active{background:var(--nav-active);padding:0 24px}

/* hero */
.hero{left:0;top:149px;width:1200px;height:450px;background:linear-gradient(90deg,#f3f3f3 0%,#e2e3e6 45%,#d3d5d9 70%,#ececec 100%)}
.hero-portrait{left:750px;top:175px;width:335px;height:424px;background:linear-gradient(#e8e6e4,#f5f5f5);border-radius:160px 160px 0 0}
.hero-copy{left:116px;top:290px;color:var(--ink)}
.hero-copy .lead{font-size:50px;font-weight:300;line-height:1.05}
.hero-copy h1{font-size:50px;font-weight:600;line-height:1.1}
.hero-copy p{font-size:28px;font-weight:400;letter-spacing:1px;margin-top:6px;color:#222}
.dots{left:578px;top:573px;display:flex;gap:9px}
.dots span{width:7px;height:7px;border-radius:50%;background:var(--white)}
.dots span.on{background:#333}

/* section titles */
.center-title{left:0;width:1200px;text-align:center;font-size:25px;color:var(--ink)}

/* services */
.service{width:300px;text-align:center}
.service .pic{width:178px;height:178px;margin:0 auto;border-radius:50%;border:3px solid #eee;box-shadow:0 0 0 1px #ddd}
.service h3{margin-top:40px;font-size:19px;font-weight:400;color:var(--ink);letter-spacing:.5px}
.service p{margin-top:8px;font-size:12.5px;line-height:19px;color:var(--text)}
.btn{display:inline-block;background:linear-gradient(#5b6a9c,var(--btn-dark));color:var(--white);font-size:13px;border-radius:2px}
.service .btn{margin-top:20px;width:101px;height:29px;line-height:29px}

/* about */
.about-band{left:0;top:1101px;width:1200px;height:320px;background:var(--band)}
.about-pic{left:120px;top:1136px;width:350px;height:245px;border:2px solid var(--white);box-shadow:0 0 0 1px #ddd;background:linear-gradient(135deg,#4f9fd0,#bcd8ea 50%,#3b8ec2)}
.about-copy{left:493px;top:1133px;width:587px}
.about-copy h2{font-size:25px;font-weight:400;color:var(--ink)}
.about-copy p{margin-top:10px;font-size:12.5px;line-height:20.3px}
.about-copy .btn{margin-top:26px;width:101px;height:30px;line-height:30px;text-align:center}

/* team */
.row-title{left:120px;width:960px;font-size:22px;color:var(--ink);border-bottom:1px solid var(--line);padding-bottom:6px}
.team-arrows{left:1021px;top:1458px;display:flex;gap:2px}
.team-arrows span{width:28px;height:24px;background:#eee;border:1px solid #ddd;display:flex;align-items:center;justify-content:center}
.member{top:1519px;width:224px;height:140px;border:2px solid var(--white);box-shadow:0 0 0 1px #ccc}

/* appointment */
.field{border:2px solid #ddd;background:var(--white);font-size:13px;color:#aaa;padding:0 12px;display:flex;align-items:center}
.field.area{align-items:flex-start;padding-top:8px}
.submit{left:123px;top:1874px;width:154px;height:41px;line-height:41px;text-align:center;font-size:18px;font-weight:600;background:linear-gradient(#6474a6,var(--btn-dark));color:var(--white);border-radius:2px}
.consent{right:120px;top:1901px;font-size:11.5px;color:#999;display:flex;align-items:center;gap:12px}
.consent i{width:14px;height:14px;border:1px solid #ccc;display:block}

/* footer */
.footer{left:0;top:1971px;width:1200px;height:277px;background:var(--footer)}
.f-col{top:1988px;color:var(--footer-text)}
.f-col h4{font-size:19px;font-weight:400;color:var(--white);margin-bottom:18px}
.f-col ul{list-style:none;font-size:12.5px;line-height:18px}
.f-col li.active{color:var(--nav-active)}
.f-col p{font-size:12.5px;line-height:20px;width:205px}
.social{display:flex;gap:10px;margin-top:14px}
.social span{width:20px;height:20px;border-radius:50%;background:#bbb}
.f-field{background:var(--white);font-size:9px;color:#888;padding:4px 7px}
.send{left:969px;top:2204px;width:111px;height:29px;line-height:29px;text-align:center;background:var(--green);color:var(--white);font-size:13px;border-radius:2px}
.copyright{left:0;top:2248px;width:1200px;height:33px;line-height:33px;background:var(--footer-bar);color:#ccc;font-size:12.5px;text-align:center}
</style>
</head>
<body>

<header>
  <div class="abs logo">Colin Ashford, DDS</div>
  <div class="abs callout">
    <div class="phone">Call: <b>+123 555 0148</b></div>
    <div class="tag">For Free Consultancy We are here for You 24/7</div>
    <svg width="38" height="38" viewBox="0 0 38 38" aria-hidden="true">
      <circle cx="22" cy="18" r="13" fill="none" stroke="#555" stroke-width="2"/>
      <text x="22" y="23" text-anchor="middle" font-family="Open Sans,Arial,sans-serif" font-size="12" font-weight="600" fill="#444">24</text>
      <path d="M3 10c2-4 6-4 8 0l-3 4c1 4 4 7 8 9l3-3c4 1 5 5 1 8-6 3-19-8-17-18z" fill="#555"/>
    </svg>
  </div>
</header>

<nav class="abs nav">
  <ul>
    <li class="active">Home</li><li>Our Team</li><li>Philosophy</li><li>Restorative</li><li>Cosmetic</li><li>Tooth Replacement</li><li>First Visit Contact</li>
  </ul>
</nav>

<section>
  <div class="abs hero" role="img" aria-label="Softly blurred city skyline behind the hero text"></div>
  <div class="abs hero-portrait" role="img" aria-label="Portrait of the dentist in a white coat with a stethoscope"></div>
  <div class="abs hero-copy">
    <div class="lead">I specialize in</div>
    <h1>General Dentistry</h1>
    <p>Teeth Whitening Solutions for Everyone</p>
  </div>
  <div class="abs dots"><span></span><span class="on"></span><span></span></div>
</section>

<section>
  <h2 class="abs center-title" style="top:637px;font-weight:400">Our Work</h2>
  <div class="abs service" style="left:113px;top:690px">
    <div class="pic" role="img" aria-label="Close-up of a bright smile" style="background:radial-gradient(#fff 20%,#e9a49a 55%,#f5e3df)"></div>
    <h3>RESTORATIVE</h3>
    <p>Sed ut perspiciatis unde omnis iste natus error sit totam rem aperiam, eaque ipsa quae ab illo inventore .</p>
    <span class="btn">Read More »</span>
  </div>
  <div class="abs service" style="left:449px;top:690px">
    <div class="pic" role="img" aria-label="Patient receiving a dental check-up" style="background:linear-gradient(135deg,#e8cdb9,#9fc4e4 60%,#4e8fd0)"></div>
    <h3>PREVENTIVE</h3>
    <p>Sed ut perspiciatis unde omnis iste natus error sit totam rem aperiam, eaque ipsa quae ab illo inventore .</p>
    <span class="btn">Read More »</span>
  </div>
  <div class="abs service" style="left:784px;top:690px">
    <div class="pic" role="img" aria-label="Set of dentures on a grey surface" style="background:radial-gradient(#f1b2a8 15%,#a7a9b1 60%,#6f7380)"></div>
    <h3>REPLACEMENT</h3>
    <p>Sed ut perspiciatis unde omnis iste natus error sit totam rem aperiam, eaque ipsa quae ab illo inventore .</p>
    <span class="btn">Read More »</span>
  </div>
</section>

<section>
  <div class="abs about-band"></div>
  <div class="abs about-pic" role="img" aria-label="Group photo of the dental team in scrubs and coats"></div>
  <div class="abs about-copy">
    <h2>About Our Team</h2>
    <p>Lorem ipsum dolor sit amet consectetur adipisicing elit sed do eiusmod tempor incididunt ut labore et dolore magna aliqua ut enim ad minim veniam quis nostrud exercitation ullamco laboris nisi ut aliquip ex ea commodo consequat duis aute irure dolor.in reprehenderit in voluptate velit esse cillum dolore fugiat nulla pariatur. Excepteur sint occaecat cupidatat non proident, sunt in culpa qui officia deserunt mollit anim id est laborum aliquip ex ea commodo consequat duis aute irure dolor.in reprehenderit in voluptate velit esse cillum dolore eu fugiat nulla pariatur. Excepteur sint occaecat cupidatat non proident, sunt in</p>
    <span class="btn">Read More</span>
  </div>
</section>

<section>
  <h2 class="abs row-title" style="top:1457px;font-weight:400">OUR TEAM</h2>
  <div class="abs team-arrows">
    <span><svg width="8" height="12" viewBox="0 0 8 12"><path d="M6 1L1 6l5 5" fill="none" stroke="#999" stroke-width="1.5"/></svg></span>
    <span><svg width="8" height="12" viewBox="0 0 8 12"><path d="M2 1l5 5-5 5" fill="none" stroke="#999" stroke-width="1.5"/></svg></span>
  </div>
  <div class="abs member" style="left:120px;background:linear-gradient(#d9dde2,#f2f2f2)" role="img" aria-label="Portrait of a senior dentist"></div>
  <div class="abs member" style="left:365px;background:linear-gradient(#8ec9e4,#e7f1f6)" role="img" aria-label="Portrait of a female dentist"></div>
  <div class="abs member" style="left:610px;background:linear-gradient(#e6e6e6,#c9cdd1)" role="img" aria-label="Portrait of a dentist holding a tablet"></div>
  <div class="abs member" style="left:856px;background:linear-gradient(#7d7f84,#d7d3cf)" role="img" aria-label="Portrait of a smiling female dentist"></div>
</section>

<section>
  <h2 class="abs row-title" style="top:1712px;font-weight:400;font-size:25px">Request an Appointment</h2>
  <div class="abs field" style="left:120px;top:1772px;width:329px;height:41px">Name</div>
  <div class="abs field" style="left:459px;top:1772px;width:327px;height:41px">Phone</div>
  <div class="abs field area" style="left:795px;top:1772px;width:285px;height:90px">Message</div>
  <div class="abs field" style="left:120px;top:1821px;width:329px;height:41px">E-mail</div>
  <div class="abs field" style="left:459px;top:1821px;width:327px;height:41px;justify-content:space-between">Date <span style="font-size:9px">▼</span></div>
  <div class="abs submit">Submit</div>
  <div class="abs consent"><i></i>Lorem ipsum dolor sit amet consectetur Adipisicing elit sed do.</div>
</section>

<footer>
  <div class="abs footer"></div>
  <div class="abs f-col" style="left:120px">
    <h4>Site Link</h4>
    <ul><li class="active">Home</li><li>Our Team</li><li>Philosophy</li><li>Restorative</li><li>Cosmetic</li><li>Tooth Replacement</li><li>First Visit Contact</li></ul>
  </div>
  <div class="abs f-col" style="left:304px">
    <h4>Lorem ipsum</h4>
    <ul><li>Replacement</li><li>Preventive</li><li>Restorative</li><li>Cosmetic</li></ul>
  </div>
  <div class="abs f-col" style="left:500px">
    <h4>Contact Us</h4>
    <p>Lorem ipsum dolor sit amet consectetur adipisicing elit sed do eiusmod tempor</p>
    <div class="social"><span></span><span></span><span></span><span></span></div>
  </div>
  <div class="abs f-col" style="left:785px"><h4>Contact Form</h4></div>
  <div class="abs f-field" style="left:785px;top:2036px;width:143px;height:20px">First Name</div>
  <div class="abs f-field" style="left:940px;top:2036px;width:140px;height:20px">Last Name</div>
  <div class="abs f-field" style="left:785px;top:2067px;width:143px;height:20px">Phone</div>
  <div class="abs f-field" style="left:940px;top:2067px;width:140px;height:20px">Email</div>
  <div class="abs f-field" style="left:785px;top:2096px;width:295px;height:94px">Message</div>
  <div class="abs send">Send Message</div>
  <div class="abs copyright">Copy Right © 2014 ColinAshford.dds. All Rights Reserved.</div>
</footer>

</body>
</html>
```